Garlic Farm for Farm Sales/Restaurant sales

Need a professional, but appealing to agriculture world. We are selling 27 kinds of Organic Garlic from a farm in Simla,CO. I have uploaded logo and business information-we are going to need a template, because I will need to use it for four separate people.
-We are trying to appeal to Farm to table restaurants
-As well as growers/farmers

Target Market(s)

Agriculture Sales/Restaurants-Organic

Industry/Entity Type

Agriculture

Contact Information for Business Card

Want it to look more unique then your average kelto stock card- I want it to look amazing

Font styles to use
Sans Serif

Colors
0455a3
ec1f27
fbed22
ffffff

Requirements
Must have
• Just be creative
Nice to have
• Colorful
Should not have
• plain

```html
<!DOCTYPE html>
<html lang="en">
<head>
<meta charset="utf-8">
<title>Ridge Clove Garlic – Business Card</title>
<link rel="stylesheet" href="https://fonts.googleapis.com/css2?family=Questrial&family=Caveat:wght@500&display=swap">
<style>
  :root {
    --page-bg: #d9d6d2;
    --card-light: #f1f2f3;
    --card-light-edge: #e2e4e7;
    --navy-deep: #0a1634;
    --navy: #1b2a55;
    --brand-red: #b5202b;
    --gold: #e4a91e;
    --gold-soft: #f0b93a;
    --text-light: #e9ecf3;
    --logo-navy: #1b2a55;
  }
  * { margin: 0; padding: 0; box-sizing: border-box; }
  html, body {
    width: 1200px; height: 969px; overflow: hidden;
    background: var(--page-bg);
  }
  .stage {
    position: relative; width: 1200px; height: 969px;
  }
  .business-card {
    position: absolute; left: 100px; top: 200px;
    width: 1000px; height: 570px;
    border-radius: 34px; overflow: hidden;
    background: linear-gradient(160deg, var(--card-light), var(--card-light-edge));
    box-shadow: 0 14px 40px rgba(0,0,0,.18);
  }
  .card-shapes { position: absolute; inset: 0; }
  .brand-block {
    position: absolute; left: 60px; top: 130px; width: 400px;
    display: flex; flex-direction: column; align-items: center; gap: 26px;
  }
  .brand-dot {
    width: 120px; height: 120px; border-radius: 50%;
    background: var(--brand-red);
  }
  .brand-name {
    font-family: "Questrial", sans-serif;
    font-size: 50px; line-height: 1.05; text-align: center;
    color: var(--logo-navy);
  }
  .contact-block {
    position: absolute; right: 52px; top: 100px;
    text-align: right;
    font-family: "Questrial", sans-serif;
    color: var(--text-light);
  }
  .person-name {
    font-family: "Caveat", cursive;
    font-size: 50px; font-weight: 500; color: var(--gold-soft);
    line-height: 1;
  }
  .person-title { font-size: 24px; margin-top: 10px; }
  .address { font-size: 26px; line-height: 38px; margin-top: 26px; }
  .contact-list { list-style: none; margin-top: 14px; font-size: 26px; }
  .contact-list li {
    display: flex; justify-content: flex-end; align-items: center;
    gap: 10px; line-height: 40px;
  }
  .contact-list svg { width: 22px; height: 22px; fill: var(--gold); }
  .social-row {
    display: flex; justify-content: flex-end; gap: 8px; margin-top: 14px;
  }
  .social-dot {
    width: 28px; height: 28px; border-radius: 50%;
    border: 2px solid var(--gold);
  }
</style>
</head>
<body>
<main class="stage">
  <section class="business-card">
    <svg class="card-shapes" viewBox="0 0 1000 570" width="1000" height="570" aria-hidden="true">
      <defs>
        <linearGradient id="navyPanel" x1="0" y1="0" x2="1" y2="1">
          <stop offset="0" stop-color="#1b2a55"/>
          <stop offset="1" stop-color="#0a1634"/>
        </linearGradient>
      </defs>
      <path d="M520 0 C600 50 620 170 585 240 C650 180 640 60 565 0 Z" fill="var(--brand-red)"/>
      <path d="M560 0 L1000 0 L1000 570 L560 570 C520 500 505 420 535 330 C565 245 620 130 560 0 Z" fill="url(#navyPanel)"/>
      <path d="M548 330 C515 430 545 520 610 570 L596 570 C540 520 512 430 548 330 Z" fill="var(--gold)"/>
    </svg>

    <div class="brand-block">
      <div class="brand-dot"></div>
      <div class="brand-name">Ridge Clove<br>Garlic</div>
    </div>

    <div class="contact-block">
      <div class="person-name">Dale Fenwick</div>
      <div class="person-title">CEO/Founder</div>
      <div class="address">P.O. Box 72<br>Ardell, CO &nbsp;80412</div>
      <ul class="contact-list">
        <li>719-555-0143
          <svg viewBox="0 0 24 24"><path d="M6.6 10.8a15.1 15.1 0 0 0 6.6 6.6l2.2-2.2c.3-.3.7-.4 1-.2 1.1.4 2.3.6 3.6.6.6 0 1 .4 1 1V20c0 .6-.4 1-1 1A17 17 0 0 1 3 4c0-.6.4-1 1-1h3.5c.6 0 1 .4 1 1 0 1.3.2 2.5.6 3.6.1.3 0 .7-.2 1z"/></svg>
        </li>
        <li>Nora@RidgeClove.com
          <svg viewBox="0 0 24 24"><path d="M2 5h20v14H2z M3.5 6.5 12 13l8.5-6.5" stroke="#0a1634" stroke-width="1.5"/></svg>
        </li>
        <li>www.RidgeClove.com
          <svg viewBox="0 0 24 24"><circle cx="12" cy="12" r="10"/><path d="M2 12h20M12 2c3 3 3 17 0 20M12 2c-3 3-3 17 0 20" stroke="#0a1634" stroke-width="1.4" fill="none"/></svg>
        </li>
      </ul>
      <div class="social-row">
        <span class="social-dot"></span>
        <span class="social-dot"></span>
        <span class="social-dot"></span>
        <span class="social-dot"></span>
      </div>
    </div>
  </section>
</main>
</body>
</html>
```